Global (re)insurance broker needs a business card design

We need a classic business card for our company that is headquartered in SG, with offices in Malaysia and Dubai. We specialise in insurance and reinsurance broking and consultancy for our global clients.

```html
<!DOCTYPE html>
<html lang="en">
<head>
<meta charset="utf-8">
<title>Norvane Business Card</title>
<link rel="stylesheet" href="https://fonts.googleapis.com/css2?family=Open+Sans:wght@400;600;700&display=swap">
<style>
  :root {
    --stage: #e9e6e1;
    --card: #1f1f24;
    --card-deep: #141417;
    --ink: #f2f2f2;
    --brand-green: #b7d3a8;
    --brand-blue: #2c4ea6;
    --ghost: #2b2b31;
  }
  * { box-sizing: border-box; margin: 0; padding: 0; }
  html, body { width: 1200px; height: 780px; overflow: hidden; }
  body {
    background: var(--stage);
    font-family: "Open Sans", Arial, sans-serif;
    position: relative;
  }
  .card {
    position: absolute;
    top: 230px;
    width: 560px;
    height: 320px;
    border-radius: 4px;
    overflow: hidden;
    box-shadow: 0 10px 30px rgba(0,0,0,0.25);
  }
  .card--front { left: 30px; background: var(--card); }
  .card--back { left: 610px; background: var(--card-deep); }

  .wordmark {
    position: absolute;
    left: 30px;
    top: 20px;
    font-size: 58px;
    font-weight: 600;
    letter-spacing: 1px;
    color: var(--brand-green);
    line-height: 1;
  }
  .contact {
    position: absolute;
    left: 30px;
    top: 118px;
    color: var(--ink);
    font-size: 13px;
    line-height: 1.45;
    list-style: none;
  }
  .contact__address { margin-bottom: 4px; }
  .contact__row { display: flex; align-items: center; gap: 8px; }
  .contact__icon { width: 12px; height: 12px; flex: none; }

  .person {
    position: absolute;
    right: 40px;
    top: 186px;
    text-align: right;
  }
  .person__name {
    font-size: 28px;
    font-weight: 700;
    color: var(--brand-blue);
    line-height: 1.1;
  }
  .person__title {
    font-size: 14px;
    color: var(--ink);
  }
  .accent-bar {
    position: absolute;
    right: 0;
    top: 192px;
    width: 16px;
    height: 56px;
    background: var(--brand-green);
  }
  .ghost-mark {
    position: absolute;
    left: 170px;
    bottom: -14px;
    font-size: 86px;
    font-weight: 600;
    color: var(--ghost);
    line-height: 1;
    letter-spacing: 1px;
  }

  .back-pattern {
    position: absolute;
    inset: 0;
    background: linear-gradient(120deg, #141417 0%, #1d1d22 55%, #55555c 85%, #2a2a2f 100%);
  }
  .back-mark {
    position: absolute;
    left: 50%;
    top: 62%;
    transform: translate(-50%, -50%);
    font-size: 20px;
    font-weight: 600;
    color: var(--brand-green);
    background: var(--card-deep);
    padding: 2px 8px;
  }
</style>
</head>
<body>
  <section class="card card--front">
    <div class="wordmark">NORVANE</div>
    <ul class="contact">
      <li class="contact__address">22 Harbour Lane, Meridian Tower<br>#08-04, Singapore 048620</li>
      <li class="contact__row">
        <svg class="contact__icon" viewBox="0 0 12 12"><rect x="3" y="0.5" width="6" height="11" rx="1" fill="none" stroke="#b7d3a8" stroke-width="1.2"/><circle cx="6" cy="9.5" r="0.7" fill="#b7d3a8"/></svg>
        +65 8123 4567
      </li>
      <li class="contact__row">
        <svg class="contact__icon" viewBox="0 0 12 12"><circle cx="6" cy="6" r="5.2" fill="none" stroke="#2c4ea6" stroke-width="1.2"/><ellipse cx="6" cy="6" rx="2.2" ry="5.2" fill="none" stroke="#2c4ea6" stroke-width="1"/><line x1="0.8" y1="6" x2="11.2" y2="6" stroke="#2c4ea6" stroke-width="1"/></svg>
        www.norvane.com
      </li>
      <li class="contact__row">
        <svg class="contact__icon" viewBox="0 0 12 12"><rect x="0.6" y="2.2" width="10.8" height="7.6" fill="none" stroke="#b7d3a8" stroke-width="1.2"/><polyline points="0.8,2.6 6,6.8 11.2,2.6" fill="none" stroke="#b7d3a8" stroke-width="1.1"/></svg>
        mira@norvane.com
      </li>
    </ul>
    <div class="person">
      <div class="person__name">Mira Lowe</div>
      <div class="person__title">Chief Operating Officer</div>
    </div>
    <div class="accent-bar"></div>
    <div class="ghost-mark">NORVANE</div>
  </section>

  <section class="card card--back">
    <div class="back-pattern" role="img" aria-label="Repeating company name pattern across the card back"></div>
    <div class="back-mark">NORVANE</div>
  </section>
</body>
</html>
```